Build PowerPoint for New Logo & Letterhead

I have started my own consulting firm and created a logo and letterhead (attached) am looking PowerPoint template. My name is Dorrit Vandermolen and the company is called K Quadrant Advisory. We primarily use PowerPoint files to display analyses, maps and key talking points from interviews and/or recommendations. We use the documents more to facilitate discussion with our target audiences. Most of the time our PowerPoint document is printed as handouts for our clients and not projected.

Target Market(s)

Healthcare provider organizations (hospitals, health systems, physician groups)

Industry/Entity Type

Healthcare

Font styles to use
Sans Serif

Colors
abd036
1f9ad1
0355a3

Requirements
Must have
• I would like to cover page to play off of the letterhead in some fashion. I want the design to provide plenty of space for text, graphics, maps, pictures, etc.
• We will usually include our clients logo somewhere on the document. Historically it is prominent on the cover page and then in one of the corners on all of the pages thereafter.

```html
<!DOCTYPE html>
<html lang="en">
<head>
<meta charset="utf-8">
<title>Project Title Here</title>
<link href="https://fonts.googleapis.com/css2?family=Roboto+Condensed:wght@400;700&display=swap" rel="stylesheet">
<style>
  :root {
    --blue-deep: #0355a3;
    --blue-mid: #1f9ad1;
    --blue-bright: #09a6ee;
    --blue-band: #2f82c2;
    --blue-total: #3584c4;
    --green: #abd036;
    --green-dark: #9bc73a;
    --ink: #2b3442;
    --rule: #d4d7db;
    --grey-total: #808080;
    --page: #f8f9fb;
    --white: #ffffff;
  }
  * { margin: 0; padding: 0; box-sizing: border-box; }
  html, body { width: 1200px; height: 900px; overflow: hidden; }
  body {
    position: relative;
    background: var(--page);
    font-family: "Roboto Condensed", "Arial Narrow", sans-serif;
    color: var(--ink);
  }
  .title-bar { position: absolute; left: 0; top: 0; width: 1200px; height: 80px; }
  .project-title {
    position: absolute; left: 22px; top: 14px;
    font-size: 39px; font-weight: 700; color: var(--white); letter-spacing: 0.3px;
  }
  .brand-name {
    position: absolute; right: 28px; top: 26px;
    display: flex; align-items: center; gap: 8px;
    font-size: 21px; font-weight: 700; color: var(--blue-deep);
  }
  .brand-name .mark { width: 14px; height: 14px; background: var(--green); }
  .subtitle-band {
    position: absolute; left: 0; top: 172px; width: 1200px; height: 53px;
    background: var(--blue-band);
    color: var(--white); font-size: 30px; font-weight: 700;
    padding: 8px 0 0 22px;
  }
  .expense-table {
    position: absolute; left: 18px; top: 235px; width: 1182px;
    border-collapse: collapse; table-layout: fixed;
    font-size: 22px;
  }
  .expense-table col.label { width: 424px; }
  .expense-table col.year { width: 159px; }
  .expense-table col.year-mid { width: 160px; }
  .expense-table col.total { width: 282px; }
  .expense-table th {
    height: 50px; color: var(--white); font-weight: 700; font-size: 24px;
    text-align: center;
  }
  .expense-table th.empty { background: transparent; border-bottom: 1px solid var(--rule); }
  .expense-table th.y2016 { background: var(--blue-deep); }
  .expense-table th.y2017 { background: var(--blue-mid); border-left: 3px solid var(--white); }
  .expense-table th.y2018 { background: var(--green-dark); border-left: 3px solid var(--white); }
  .expense-table th.grand { background: var(--blue-total); font-size: 20px; border-left: 3px solid var(--white); }
  .expense-table td {
    height: 48px; border-bottom: 1px solid var(--rule); border-left: 1px solid var(--rule);
    white-space: nowrap;
  }
  .expense-table tbody tr:first-child td { height: 60px; }
  .expense-table td.item { border-left: none; padding-left: 4px; }
  .expense-table td.amount { padding-left: 27px; }
  .expense-table td.blank { text-align: center; }
  .expense-table td.grand {
    background: var(--blue-total); color: var(--white); text-align: center;
    border-bottom: 1px solid var(--white); border-left: 3px solid var(--white);
  }
  .expense-table tfoot td {
    height: 47px; background: var(--grey-total); color: var(--white);
    border: none;
  }
  .expense-table tfoot td.item { padding-left: 4px; }
  .expense-table tfoot td.sum { font-weight: 700; text-align: center; padding-left: 28px; }
  .expense-table tfoot td.grand { background: var(--blue-total); border-left: 3px solid var(--white); border-top: 1px solid var(--white); font-weight: 400; }
  .footer { position: absolute; left: 0; top: 843px; width: 1200px; height: 57px; }
  .copyright {
    position: absolute; left: 25px; top: 857px;
    font-size: 21px; color: var(--white);
  }
</style>
</head>
<body>
  <svg class="title-bar" viewBox="0 0 1200 80" aria-hidden="true">
    <defs>
      <linearGradient id="titleFill" x1="0" x2="1" y1="0" y2="0">
        <stop offset="0" stop-color="#0a6cbf"/>
        <stop offset="1" stop-color="#09a6ee"/>
      </linearGradient>
    </defs>
    <rect width="1200" height="80" fill="#ffffff"/>
    <polygon points="0,0 1050,0 1002,80 0,80" fill="url(#titleFill)"/>
  </svg>
  <h1 class="project-title">PROJECT TITLE HERE</h1>
  <div class="brand-name"><span class="mark"></span>K Quadrant Advisory</div>

  <h2 class="subtitle-band">SUBTEXT TITLE HERE</h2>

  <table class="expense-table">
    <colgroup>
      <col class="label"><col class="year"><col class="year-mid"><col class="year"><col class="total">
    </colgroup>
    <thead>
      <tr>
        <th class="empty"></th>
        <th class="y2016">KQ 2016</th>
        <th class="y2017">KQ 2017</th>
        <th class="y2018">KQ 2018</th>
        <th class="grand">GRAND TOTAL</th>
      </tr>
    </thead>
    <tbody>
      <tr><td class="item">Lorem Ipsum dolor sit text here text here</td><td class="amount">3642.95 $</td><td class="blank">$</td><td class="blank">$</td><td class="grand">3643 $</td></tr>
      <tr><td class="item">Lorem Ipsum dolor sit text here text here</td><td class="amount">0000.00 $</td><td class="blank"></td><td class="blank"></td><td class="grand">0$</td></tr>
      <tr><td class="item">Lorem Ipsum dolor sit text here text here</td><td class="amount">1096.58 $</td><td class="blank"></td><td class="blank"></td><td class="grand">1097$</td></tr>
      <tr><td class="item">Lorem Ipsum dolor sit text here text here</td><td class="amount">592.84$</td><td class="blank"></td><td class="blank"></td><td class="grand">593 $</td></tr>
      <tr><td class="item">Lorem Ipsum dolor sit text here text here</td><td class="amount">4345.21$</td><td class="blank"></td><td class="blank"></td><td class="grand">4345$</td></tr>
      <tr><td class="item">Lorem Ipsum dolor sit text here text here</td><td class="amount">3.97$</td><td class="blank"></td><td class="blank"></td><td class="grand">4$</td></tr>
      <tr><td class="item">Lorem Ipsum dolor sit text here text here</td><td class="amount">391.77$</td><td class="blank"></td><td class="blank"></td><td class="grand">392$</td></tr>
      <tr><td class="item">Lorem Ipsum dolor sit text here text here</td><td class="amount">438.81$</td><td class="blank"></td><td class="blank"></td><td class="grand">439$</td></tr>
      <tr><td class="item">Lorem Ipsum dolor sit text here text here</td><td class="amount">0$</td><td class="blank"></td><td class="blank"></td><td class="grand">0$</td></tr>
    </tbody>
    <tfoot>
      <tr><td class="item">Total Expenses</td><td class="sum">10,512.13$</td><td></td><td></td><td class="grand">1051$2</td></tr>
    </tfoot>
  </table>

  <svg class="footer" viewBox="0 0 1200 57" aria-hidden="true">
    <rect x="0" y="27" width="1200" height="30" fill="#a9d13f"/>
    <polygon points="0,0 247,0 272,27 272,57 0,57" fill="#9bc73a"/>
  </svg>
  <p class="copyright">Copyright text here</p>
</body>
</html>
```